Product label for herbal salves, lotions, soaps and tinctures

We need a very simple, clean and organic looking label that can be used for an ointment jar, a lotion bottle and a dropper bottle.
We have an existing logo (see attached). We like the colors white, olive green, gold and black. It needs to include product name as dominant and logo. It also needs to include an ingredient list, and usage statement. Include weight of product, distributed by, made in the USA, and QVX statement.
Example of what needs to be present:
Logo
Name: Tranquil Ease Blend
Used for: For Muscle Aches, Arthritis, Tendonitis, Headaches
To Use: For muscle aches, arthritis and tendonitis, massage into affected area. For tension headache apply to neck, temples and forehead.
Store in a cool and dry place, away from direct heat and sunlight.
Weight of product: 1.75
DIST. BY: Copper Brook Herbal
Made in the USA
This product is not intended to diagnose, treat, cure
or prevent any disease. Not regulated
by the QVX. Please consult your health care practitioner
before using product. Discontinue use if any adverse reaction occurs.
Ingredient list:
Wildcrafted Ingredients:
Ashwagandha Root, Peppermint Leaf, Hops Flowers, St. John’s Wort Herb, Arnica Flowers, Green Tea Leaf, Alfalfa Leaf, Dandelion Root, Burdock Root, Chickweed Herb, Chaparral Leaf, Yarrow Flowers, Boneset Herb, Moringa Leaf, Meadowsweet Herb, Nettle Leaf
Organic Ingredients:
Olive Oil, Aloe Leaf, Sweet Birch Bark, Helichrysum Flowers, Holy Basil Leaf, Borage Herb, Ginger Root, Angelica Root, White Willow Bark, Mustard Seed, Beeswax, Vitamin E, Essential Oils
Dimensions of Jar:
Circumference: 7 in.
Height: 1 in.

```html
<!DOCTYPE html>
<html lang="en">
<head>
<meta charset="utf-8">
<title>Copper Brook Herbal – Tranquil Ease Blend Label</title>
<link href="https://fonts.googleapis.com/css2?family=Quicksand:wght@500;600&family=Questrial&family=Roboto+Condensed:wght@500&display=swap" rel="stylesheet">
<style>
  :root {
    --olive: #6b6d2b;
    --gold: #d6a137;
    --ink: #4a4a4a;
    --paper: #ffffff;
    --leaf-light: #e9eae2;
    --leaf-mid: #c9cbbf;
  }
  * { margin: 0; padding: 0; box-sizing: border-box; }
  html, body {
    width: 1200px; height: 810px; overflow: hidden;
    background: var(--paper);
  }
  .label-set {
    position: relative; width: 1200px; height: 810px;
  }
  .panel {
    position: absolute; top: 324px; height: 162px;
  }
  .panel--usage, .panel--ingredients {
    background: var(--olive); color: var(--paper);
    font-family: "Questrial", sans-serif;
    text-align: center;
  }
  .panel--usage { left: 30px; width: 404px; padding-top: 15px; }
  .panel--front { left: 450px; width: 300px; background: var(--paper); }
  .panel--ingredients { left: 769px; width: 401px; padding: 24px 26px 0; }

  .usage__directions { font-size: 9.6px; line-height: 15.5px; }
  .usage__facts { margin-top: 14px; font-size: 7.4px; line-height: 15.2px; }
  .usage__facts .gap { display: inline-block; width: 22px; }

  .ingredients__list { font-size: 7.4px; line-height: 15.1px; }

  .branch {
    position: absolute; top: 0; height: 78px;
    background: linear-gradient(135deg, var(--leaf-light), var(--leaf-mid) 60%, var(--leaf-light));
    opacity: .75;
  }
  .branch--left { left: 0; width: 110px; border-bottom-right-radius: 60px 40px; }
  .branch--right { right: 0; width: 120px; border-bottom-left-radius: 60px 40px; }

  .brand {
    position: absolute; left: 0; right: 0; top: 40px;
    display: flex; align-items: center; justify-content: center; gap: 6px;
    font-family: "Quicksand", sans-serif; font-weight: 600;
    font-size: 17px; color: var(--olive);
  }
  .brand__mark {
    width: 12px; height: 12px; border-radius: 50%; background: var(--gold);
  }
  .product-name {
    position: absolute; left: 0; right: 0; top: 108px;
    font-family: "Quicksand", sans-serif; font-weight: 500;
    font-size: 23px; color: var(--ink); text-align: center; letter-spacing: .3px;
  }
  .product-rule {
    position: absolute; left: 36px; right: 36px; top: 142px;
    height: 1.5px; background: var(--gold);
  }
  .product-use {
    position: absolute; left: 0; right: 0; top: 146px;
    font-family: "Roboto Condensed", sans-serif; font-weight: 500;
    font-size: 7.8px; color: var(--olive); text-align: center;
  }
</style>
</head>
<body>
<main class="label-set">
  <section class="panel panel--usage">
    <p class="usage__directions">For muscle aches, arthritis and tendonitis, massage into affected area.<br>For tension headache apply to neck, temples and forehead.</p>
    <p class="usage__facts">
      Store in a cool and dry place, away from direct heat and sunlight.<br>
      Weight of product: 1.75<span class="gap"></span>DIST. BY: Copper Brook Herbal<br>
      MADE IN THE USA<br>
      This product is not intended to diagnose, treat, cure&nbsp; or prevent any disease.<br>
      Not regulated by the QVX. Please consult your health care practitioner<br>
      before using product. Discontinue use if any adverse reaction occurs.
    </p>
  </section>

  <section class="panel panel--front">
    <div class="branch branch--left" role="img" aria-label="Line drawing of an olive branch with leaves and fruit"></div>
    <div class="branch branch--right" role="img" aria-label="Line drawing of an olive branch with leaves and fruit"></div>
    <div class="brand"><span class="brand__mark"></span>Copper Brook Herbal</div>
    <h1 class="product-name">Tranquil Ease Blend</h1>
    <div class="product-rule"></div>
    <p class="product-use">For Muscle Aches, Arthritis, Tendonitis, Headaches</p>
  </section>

  <section class="panel panel--ingredients">
    <p class="ingredients__list">
      Ingredient list:<br>
      Wildcrafted Ingredients:<br>
      Ashwagandha Root, Peppermint Leaf, Hops Flowers, St. John’s Wort Herb, Arnica Flowers, Green Tea Leaf, Alfalfa Leaf, Dandelion Root, Burdock Root, Chickweed Herb, Chaparral Leaf, Yarrow Flowers, Boneset Herb, Moringa Leaf, Meadowsweet Herb, Nettle Leaf<br>
      Organic Ingredients:<br>
      Olive Oil, Aloe Leaf, Sweet Birch Bark, Helichrysum Flowers, Holy Basil Leaf, Borage Herb, Ginger Root, Angelica Root, White Willow Bark, Mustard Seed, Beeswax, Vitamin E, Essential Oils
    </p>
  </section>
</main>
</body>
</html>
```